Advertising company unique advertising platform

we need a logo design for a new company based in Australia Melbourne. We develop innovated advertising platform where consumer can use this platform to get regular discount, as business owner they can use this platform for free advertisement. Payment for this advertisement platform only payable every two weeks, when I generate revenue for their business

Industry/Entity Type

Advertising

Contact Information for Business Card

Dale Morven | Co-Founder |Managing Director
Suite 718 240 Wattlebrook Lane Melbourne Vic 3000

ABN 38 614 207 923
Tel: +61 0487 259 318 | Email: dale.morven@plivorantu.com

Font styles to use
Decorative
Script

Requirements
Must have
• Try few different design and some round corner business card
Should not have
• One round corner business card...try 4 different colour background not only black, make sure two side is designed. Be creative so imagine you are giving this to a client make sure has wow factor, if you can also try one design with engrave like all the logo, words look 3d feel
• The word Advertising Platform use attached file font

```html
<!DOCTYPE html>
<html lang="en">
<head>
<meta charset="utf-8">
<title>Kindlepoint Exchange – Business Card</title>
<link href="https://fonts.googleapis.com/css2?family=Roboto:wght@400;500;700&display=swap" rel="stylesheet">
<style>
  :root {
    --page: #e9e6e2;
    --card-dark: #262626;
    --ink-light: #f2f2f2;
    --ink-muted: #cfcfcf;
    --orange-hot: #ee5a2f;
    --orange-warm: #f7913f;
    --orange-soft: #f6a766;
    --brand: #f0743a;
    --name-ink: #2b1a12;
  }
  * { box-sizing: border-box; margin: 0; padding: 0; }
  html, body {
    width: 1200px; height: 886px; overflow: hidden;
    background: var(--page);
    font-family: "Roboto", Arial, sans-serif;
  }
  .canvas {
    width: 1200px; height: 886px;
    display: flex; align-items: center; justify-content: center; gap: 40px;
  }
  .card {
    position: relative;
    width: 540px; height: 330px;
    border-radius: 24px;
    background: var(--card-dark);
    overflow: hidden;
    box-shadow: 0 10px 30px rgba(0,0,0,.25);
  }

  /* Back side */
  .card--back .brand {
    position: absolute; top: 120px; left: 0; right: 0;
    display: flex; align-items: center; justify-content: center; gap: 14px;
  }
  .brand__dot {
    width: 22px; height: 22px; border-radius: 50%;
    background: var(--brand);
  }
  .brand__name {
    font-weight: 700; font-size: 32px; color: var(--brand);
    letter-spacing: .5px;
  }
  .card--back .website {
    position: absolute; bottom: 64px; left: 0; right: 0;
    text-align: center; color: var(--ink-light);
    font-size: 14px; letter-spacing: 5px;
  }

  /* Front side */
  .front-band { position: absolute; inset: 0; }
  .identity {
    position: absolute; left: 20px; top: 0; height: 330px; width: 110px;
  }
  .identity__text {
    position: absolute; left: 50%; top: 50%;
    transform: translate(-50%, -50%) rotate(-90deg);
    white-space: nowrap; text-align: center; color: var(--name-ink);
  }
  .identity__name { font-weight: 700; font-size: 22px; letter-spacing: .5px; }
  .identity__role { font-size: 14px; margin-top: 4px; }

  .details {
    position: absolute; left: 290px; top: 48px; right: 24px;
    color: var(--ink-light);
  }
  .details .brand__name { font-size: 27px; line-height: 1.15; display: block; margin-bottom: 26px; }
  .details p { font-size: 14px; line-height: 1.45; }
  .contact { margin-top: 4px; }
  .contact li {
    list-style: none; display: flex; align-items: center; gap: 8px;
    font-size: 14px; line-height: 1.6;
  }
  .contact svg { width: 13px; height: 13px; flex: none; }
</style>
</head>
<body>
<main class="canvas">

  <section class="card card--back" aria-label="Card back">
    <div class="brand">
      <span class="brand__dot"></span>
      <span class="brand__name">Kindlepoint Exchange</span>
    </div>
    <p class="website">www.plivorantu.com</p>
  </section>

  <section class="card card--front" aria-label="Card front">
    <svg class="front-band" viewBox="0 0 540 330" preserveAspectRatio="none" aria-hidden="true">
      <defs>
        <linearGradient id="band-fill" x1="0" y1="1" x2="1" y2="0">
          <stop offset="0" stop-color="var(--orange-hot)"/>
          <stop offset=".6" stop-color="var(--orange-warm)"/>
          <stop offset="1" stop-color="var(--orange-soft)"/>
        </linearGradient>
      </defs>
      <path d="M0 0 H230 C200 60 250 110 215 170 C185 225 240 280 205 330 H0 Z" fill="url(#band-fill)"/>
    </svg>

    <div class="identity">
      <div class="identity__text">
        <div class="identity__name">DALE MORVEN</div>
        <div class="identity__role">Co-Founder | Managing Director</div>
      </div>
    </div>

    <div class="details">
      <span class="brand__name">Kindlepoint Exchange</span>
      <p>Plivorantu Media</p>
      <p>ABN 38 614 207 923</p>
      <p>Suite 718 240 Wattlebrook Lane</p>
      <p>Melbourne Vic 3000</p>
      <ul class="contact">
        <li>
          <svg viewBox="0 0 24 24" aria-hidden="true"><path fill="var(--orange-hot)" d="M6.6 10.8a15 15 0 0 0 6.6 6.6l2.2-2.2c.3-.3.7-.4 1-.2 1.1.4 2.3.6 3.6.6.6 0 1 .4 1 1V20c0 .6-.4 1-1 1A17 17 0 0 1 3 4c0-.6.4-1 1-1h3.5c.6 0 1 .4 1 1 0 1.3.2 2.5.6 3.6.1.3 0 .7-.2 1z"/></svg>
          +61 0487 259 318
        </li>
        <li>
          <svg viewBox="0 0 24 24" aria-hidden="true"><path fill="var(--orange-hot)" d="M2 5h20v14H2z"/><path fill="none" stroke="var(--card-dark)" stroke-width="2" d="M2 5l10 8 10-8"/></svg>
          dale.morven@plivorantu.com
        </li>
      </ul>
    </div>
  </section>

</main>
</body>
</html>
```